PillPeak website blog. Simple medical advice given in clear yes or no answers that save people money

I am developing a new web page that provides medical care cost savings at the consumers' fingertips. I need a web page that is clean, concise, and attractive for me to put my valuable medical information on. The information I provide is simple to obtain, yet very valuable to the consumer, and answered in a yes or no format. For example, A person may wonder if they need an antibiotic for cold like symptoms. Seeing a doctor for an antibiotic is very expensive. But with simple and clear advice at their fingertips, they can confidently avoid having to pay $200 or more to see a doctor and get an antibiotic. This is kind of like consumer reports for medical services.

Target Market(s)

People who are savvy shoppers and want to save money on healthcare. Likely younger ages between 21 and 60, who are mobile, readily use iphones, and want strong evidence based research to guide their decisions.

Industry/Entity Type

Coding

Number of Pages Required

Colors

Requirements
Must have
• A template on the "Question" and "Answer" page that can be edited many times that can be edited many times. The Confidence rating scale would need to be edited as well. The "Date Researched" the "PillPeak Pilluminate" and "References" all need to be able to be edited. This website must be very clear and simple to understand. A medical question is posed with a yes or no answer, then answered and given a confidence rating, we then tell them how much money they saved by going to our website.
Nice to have
• We want this to be slightly fun, vibrant, warm and inviting. This will be sometime later converted into an app format. Quirky, some humor to keep it interesting.
Should not have
• No sterile looking medical images. Not boring.

```html
<!DOCTYPE html>
<html lang="en">
<head>
<meta charset="utf-8">
<title>PillPeak – Clear Valuable Health Advice</title>
<link href="https://fonts.googleapis.com/css2?family=Noto+Serif:wght@400;700&family=Roboto:wght@400;500&display=swap" rel="stylesheet">
<style>
  :root{
    --red:#e2001a;
    --blue:#145eae;
    --green:#1aab17;
    --ink:#222;
    --muted:#555;
    --nav-bg:#f4f4f4;
    --line:#dcdcdc;
    --footer-bg:#f8f8f8;
    --white:#fff;
  }
  *{box-sizing:border-box;margin:0;padding:0}
  html,body{width:1200px;height:937px;overflow:hidden;background:var(--white)}
  body{position:relative;font-family:'Roboto',sans-serif;color:var(--ink)}
  .serif{font-family:'Noto Serif',serif}

  .top-rule,.bottom-rule{position:absolute;left:0;width:1200px;height:3px;background:var(--red)}
  .top-rule{top:0}
  .bottom-rule{top:934px}

  .brand{position:absolute;left:111px;top:46px;display:flex;align-items:center;gap:10px}
  .brand-dot{width:30px;height:30px;border-radius:50%;background:var(--blue)}
  .brand-name{font-family:'Noto Serif',serif;font-weight:700;font-size:30px;color:var(--red)}

  .tagline{position:absolute;left:350px;width:500px;top:34px;text-align:center;font-family:'Noto Serif',serif;font-weight:700;font-size:27px;line-height:46px}
  .tagline .green{color:var(--green)}
  .tagline .red{color:var(--red)}
  .tagline .blue{color:var(--blue)}

  .search{position:absolute;left:932px;top:42px}
  .search-label{font-size:14px;color:#444;margin-bottom:10px}
  .search-box{width:157px;height:35px;border:1px solid #ccc;display:flex;align-items:center;justify-content:space-between;padding:0 10px;font-size:12px;font-style:italic;color:#888}

  .main-nav{position:absolute;left:0;top:141px;width:1200px;height:42px;background:var(--nav-bg);border-top:1px solid var(--line);border-bottom:1px solid var(--line)}
  .main-nav a{position:absolute;top:12px;font-size:15px;font-weight:500;color:#333;text-decoration:none;letter-spacing:.1px}
  .nav-active{position:absolute;left:111px;top:37px;width:94px;height:4px;background:var(--green)}
  .nav-active::after{content:"";position:absolute;left:39px;top:3px;border-left:8px solid transparent;border-right:8px solid transparent;border-top:8px solid var(--green)}

  .hero{position:absolute;left:0;top:183px;width:1200px;height:549px}
  .hero-photo{position:absolute;inset:0;background:linear-gradient(90deg,#c9c2b8 0%,#ddd6cd 30%,#e9e4dd 55%,#efeeec 80%,#f3f3f3 100%)}

  .topic-menu{position:absolute;left:111px;top:78px;width:289px;list-style:none}
  .topic-menu li{position:relative;height:56px;padding-left:19px;line-height:56px;font-family:'Noto Serif',serif;font-weight:700;font-size:21px;color:var(--white)}
  .topic-menu .blue{background:var(--blue)}
  .topic-menu .red{background:var(--red)}
  .topic-menu .green{background:var(--green)}
  .topic-menu .green::after{content:"";position:absolute;right:-20px;top:0;border-top:28px solid transparent;border-bottom:28px solid transparent;border-left:20px solid var(--green)}

  .hero-copy{position:absolute;left:650px;top:284px;font-family:'Noto Serif',serif;font-weight:700;font-size:43px;line-height:56px;color:var(--white);text-shadow:0 2px 4px rgba(0,0,0,.45)}
  .hero-copy .amount{color:var(--green)}
  .hero-cta{position:absolute;left:650px;top:419px;width:148px;height:47px;background:var(--blue);color:var(--white);font-family:'Noto Serif',serif;font-weight:700;font-size:17px;letter-spacing:1px;display:flex;align-items:center;justify-content:center}

  .slider-dots{position:absolute;left:1156px;top:241px;display:flex;flex-direction:column;gap:11px}
  .slider-dots span{width:15px;height:15px;border-radius:50%;border:1.5px solid #555}
  .slider-dots .current{border:4px solid var(--red);background:var(--white)}

  .site-footer{position:absolute;left:0;top:732px;width:1200px;height:202px;background:var(--footer-bg)}
  .footer-title{position:absolute;top:70px;font-family:'Noto Serif',serif;font-weight:700;font-size:17px;color:var(--ink)}
  .signup{position:absolute;left:111px;top:111px;display:flex}
  .signup-input{width:210px;height:38px;border:1px solid #ccc;background:var(--white);font-size:14px;color:#555;padding-left:14px;line-height:36px}
  .signup-send{width:43px;height:38px;background:var(--green);display:flex;align-items:center;justify-content:center}
  .legal{position:absolute;left:400px;width:400px;top:73px;text-align:center;font-size:14.5px;color:var(--muted)}
  .legal-links{margin-top:17px}
  .legal-links span{margin:0 16px}
  .ask-btn{position:absolute;left:835px;top:111px;width:253px;height:38px;background:var(--blue);border:1px solid #0d4a8c;color:var(--white);font-size:15px;display:flex;align-items:center;justify-content:center}
</style>
</head>
<body>
  <div class="top-rule"></div>

  <header>
    <div class="brand"><span class="brand-dot"></span><span class="brand-name">PillPeak</span></div>
    <div class="tagline">
      <div class="green">CLEAR VALUABLE</div>
      <div><span class="red">HEALTH ADVICE</span> <span class="blue">RIGHT NOW!</span></div>
    </div>
    <div class="search">
      <div class="search-label">Search Here:</div>
      <div class="search-box"><span>Keyword</span>
        <svg width="12" height="12" viewBox="0 0 12 12"><circle cx="5" cy="5" r="3.6" fill="none" stroke="#777" stroke-width="1.6"/><line x1="7.7" y1="7.7" x2="11" y2="11" stroke="#777" stroke-width="1.8"/></svg>
      </div>
    </div>
  </header>

  <nav class="main-nav">
    <a style="left:116px">SCREENING</a>
    <a style="left:242px">WOMEN'S HEALTH</a>
    <a style="left:414px">MEN'SHEALTH</a>
    <a style="left:558px">MEDS</a>
    <a style="left:643px">SURGERY</a>
    <a style="left:754px">IMAGING</a>
    <a style="left:860px">PEDS</a>
    <a style="left:941px">CONTACT PILLPEAK</a>
    <div class="nav-active"></div>
  </nav>

  <section class="hero">
    <div class="hero-photo" role="img" aria-label="Smiling doctor in a white coat with a stethoscope holding a tablet in a bright clinic"></div>
    <ul class="topic-menu">
      <li class="blue">Who We are?</li>
      <li class="red">How It Works</li>
      <li class="blue">How We Know</li>
      <li class="green">Evidence Based Research</li>
      <li class="blue">Dr. Whitlock</li>
      <li class="red">Who We Are Not</li>
      <li class="blue">Are We Biased?</li>
    </ul>
    <div class="hero-copy">Save <span class="amount">$1000</span> Per Year<br>on Healthcare.</div>
    <div class="hero-cta">IT's FREE!</div>
    <div class="slider-dots"><span></span><span class="current"></span><span></span></div>
  </section>

  <footer class="site-footer">
    <div class="footer-title" style="left:111px">Become A PillPeak Today!</div>
    <div class="signup">
      <div class="signup-input">Enter Email</div>
      <div class="signup-send">
        <svg width="24" height="22" viewBox="0 0 24 22"><path d="M22 1 L2 10 L9 12 L11 20 L14 14 Z M9 12 L22 1" fill="none" stroke="#fff" stroke-width="1.6" stroke-linejoin="round"/></svg>
      </div>
    </div>
    <div class="legal">
      <div>Copyright © 2018 PillPeak. All Rights Reserved.</div>
      <div class="legal-links">Disclaimer<span>|</span>Privacy Policy.</div>
    </div>
    <div class="footer-title" style="left:833px">Ask a Question here!</div>
    <div class="ask-btn">if it is working well post it!</div>
  </footer>

  <div class="bottom-rule"></div>
</body>
</html>
```